Website for new dental office

I am Dr. Colin Ashford and am building a new dental practice. I specialize in general dentistry. I am young and have a higher end dental practice incorporating very new technologies and would like my website to reflect that. As many dental patients are older, the website must be very easy to navigate. I would like patients to be able to request appointments, and will eventually add on patient information forms (the health history, etc, that you normally fill out in the practice) from my practice management software, so leave an area for that.

Industry/Entity Type

Building

```html
<!DOCTYPE html>
<html lang="en">
<head>
<meta charset="utf-8">
<title>Ashford Dental Clinic</title>
<link href="https://fonts.googleapis.com/css2?family=Open+Sans:wght@400;600&family=PT+Sans+Narrow&display=swap" rel="stylesheet">
<style>
:root{
  --sky:#10b0e3;
  --sky-light:#6fd3f3;
  --page:#f2f2f2;
  --white:#ffffff;
  --ink:#2b2b2b;
  --muted:#8a8a8a;
  --accent:#1a9fd8;
  --band:#acd6f7;
  --rule:#dcdcdc;
  --photo-a:#e9e6e3;
  --photo-b:#c9dde3;
}
*{margin:0;padding:0;box-sizing:border-box}
html,body{width:882px;height:1200px;overflow:hidden}
body{position:relative;background:var(--page);font-family:"Open Sans",Arial,sans-serif;color:var(--ink)}
.abs{position:absolute}
.header-band{left:0;top:0;width:882px;height:106px;background:linear-gradient(var(--sky-light),var(--sky) 55%,#19b6e6)}
.brand{left:97px;top:14px;font-family:"PT Sans Narrow",Arial,sans-serif;font-size:30px;color:var(--white);white-space:nowrap}
.social{display:flex;gap:4px}
.social span{width:26px;height:26px;border-radius:50%;background:var(--white);display:block}
.social--top{left:730px;top:29px}
.nav{left:97px;top:78px;width:689px;height:26px;background:linear-gradient(var(--white),#ececec);display:flex;align-items:center;padding-left:12px}
.nav a{font-size:10.5px;color:#555;text-decoration:none;margin-right:21px;letter-spacing:.1px}
.phone{left:638px;top:80px;display:flex;align-items:center;gap:4px;font-size:17px;color:#333}
.hero{left:97px;top:104px;width:689px;height:312px;background:var(--white);box-shadow:0 4px 4px rgba(0,0,0,.18)}
.hero-photo{left:106px;top:113px;width:670px;height:295px;background:linear-gradient(100deg,var(--photo-a) 0%,#f4f1ef 45%,var(--photo-b) 100%)}
.arrows{display:flex;background:var(--sky);border-radius:2px;width:52px;height:28px;align-items:center;justify-content:space-around}
.arrows--hero{left:116px;top:367px}
.arrows--testimonial{left:718px;top:882px}
.welcome-title{left:97px;top:443px;font-size:16px;font-weight:400}
.lead{left:97px;top:478px;width:420px;font-size:12px;line-height:16.5px;color:var(--accent)}
.body-text{font-size:8.6px;line-height:16.8px;color:var(--muted)}
.welcome-text{left:97px;top:522px;width:450px}
.services-title{left:98px;top:619px;font-size:16px}
.service-list{list-style:none;width:208px}
.service-list li{font-size:9px;color:#777;height:23.5px;line-height:22px;border-bottom:1px solid var(--rule);padding-left:3px}
.services-a{left:98px;top:651px}
.services-b{left:336px;top:650px;width:208px}
.appointment{left:574px;top:438px;width:210px;height:278px;background:var(--sky);padding:8px 20px 0}
.appointment h2{font-size:12px;font-weight:400;color:var(--white);margin-bottom:10px;margin-left:1px}
.field{width:168px;height:19px;background:var(--white);border-radius:2px;font-size:7px;color:#999;padding:5px 12px;margin-bottom:14px;letter-spacing:.3px}
.field--remark{height:64px;margin-bottom:13px}
.submit{width:72px;height:26px;background:var(--white);border-radius:2px;font-size:9px;font-weight:600;text-align:center;line-height:26px}
.testimonials{left:96px;top:746px;width:688px;height:176px;background:var(--band);text-align:center}
.testimonials h2{font-size:16px;font-weight:400;margin-top:28px}
.testimonials p{width:620px;margin:16px auto 0;font-size:9.4px;line-height:16.5px;color:#6c7a86;letter-spacing:.2px}
.patient{font-size:9px;color:#3d9be0;margin-top:2px}
.feature-photo{left:96px;top:946px;width:232px;height:128px;border:1px solid #cfcfcf;background:linear-gradient(120deg,#e8ecef,#c8b5a4 60%,#8f6e55)}
.feature-title{left:365px;top:942px;width:420px;font-size:16.5px;line-height:21px;font-weight:400}
.feature-text{left:362px;top:999px;width:420px;letter-spacing:.15px}
.footer{left:0;top:1116px;width:882px;height:84px;background:var(--sky)}
.footer-nav{left:96px;top:1140px;display:flex;gap:0}
.footer-nav a{font-size:9px;font-weight:600;color:var(--white);text-decoration:none;margin-right:24px}
.copyright{left:96px;top:1161px;font-size:9px;color:var(--white)}
.social--footer{left:728px;top:1145px}
</style>
</head>
<body>
<div class="abs header-band"></div>
<div class="abs brand">Ashford Dental Clinic</div>
<div class="abs social social--top" aria-label="Social links"><span></span><span></span></div>

<nav class="abs nav">
  <a href="#">HOME</a><a href="#">ABOUT</a><a href="#">SERVICES</a><a href="#">DENTISTRY</a><a href="#">REVIEWS</a><a href="#">CONTACT</a>
</nav>
<div class="abs phone">
  <svg width="15" height="15" viewBox="0 0 24 24"><path fill="#333" d="M6.6 10.8a15.1 15.1 0 0 0 6.6 6.6l2.2-2.2c.3-.3.7-.4 1-.2 1.1.4 2.3.6 3.6.6.6 0 1 .4 1 1V20c0 .6-.4 1-1 1A17 17 0 0 1 3 4c0-.6.4-1 1-1h3.5c.6 0 1 .4 1 1 0 1.3.2 2.5.6 3.6.1.3 0 .7-.2 1z"/></svg>
  555.014.2270
</div>

<section class="abs hero"></section>
<div class="abs hero-photo" role="img" aria-label="Dentist in mask examining a smiling patient's teeth"></div>
<div class="abs arrows arrows--hero">
  <svg width="8" height="10" viewBox="0 0 8 10"><path d="M6 1 2 5l4 4" stroke="#fff" stroke-width="1.6" fill="none"/></svg>
  <svg width="8" height="10" viewBox="0 0 8 10"><path d="M2 1l4 4-4 4" stroke="#fff" stroke-width="1.6" fill="none"/></svg>
</div>

<h1 class="abs welcome-title">Welcome to our Ashford Dental Clinic</h1>
<p class="abs lead">Proin gravida nibh vel velit auctor aliquet. Aenean sollicitudin, lorem quis bibendum auctor, nisi elit consequat ipsum, nec sagittis sem nibh id elit. Duis sed</p>
<p class="abs body-text welcome-text">Aenean sollicitudin, lorem quis bibendum auctor, nisi elit consequat ipsum, nec sagittis sem nibh id elit. Duis sed odio sit amet nibh vulputate cursus a sit amet mauris. Morbi accumsan ipsum velit. Nam nec tellus a odio tincidunt auctor a ornare odio. Sed non mauris vitae erat consequat auctor eu in elit. Class aptent taciti sociosqu ad litora torquent per conubia nostra, per inceptos himenaeos.</p>

<h2 class="abs services-title">Our Services</h2>
<ul class="abs service-list services-a">
  <li>The lake with its pedalos and sailboard school.</li>
  <li>Proin gravida nibh vel velit auctor aliquet.</li>
  <li>Aenean sollicitudin, lorem quis bibendum.</li>
</ul>
<ul class="abs service-list services-b">
  <li>Elit consequat ipsum, nec sagittis sem nibh it.</li>
  <li>Duis sed odio sit amet nibh vulputate cursus.</li>
  <li>Morbi accumsan ipsum velit odio tincidunt.</li>
</ul>

<form class="abs appointment">
  <h2>REQUEST AN APPOINMENT</h2>
  <div class="field">enter your name</div>
  <div class="field">enter your last name</div>
  <div class="field">enter your email id</div>
  <div class="field">enter your telephont number</div>
  <div class="field field--remark">enter your remark</div>
  <div class="submit">SUBMIT</div>
</form>

<section class="abs testimonials">
  <h2>Testimonials</h2>
  <p>Aenean sollicitudin, lorem quis bibendum auctor, nisi elit consequat ipsum, nec sagittis sem nibh id elit. Duis sed odio sit amet nibh vulputate cursus a sit amet mauris. Morbi accumsan ipsum velit. Nam nec tellus a odio tincidunt auctor a ornare odio. Sed non mauris vitae erat consequat auctor eu in elit. Class aptent taciti sociosqu ad litora torquent per conubia nostra, per inceptos himenaeos. Mauris</p>
  <div class="patient">Patient Name Here</div>
</section>
<div class="abs arrows arrows--testimonial">
  <svg width="8" height="10" viewBox="0 0 8 10"><path d="M6 1 2 5l4 4" stroke="#fff" stroke-width="1.6" fill="none"/></svg>
  <svg width="8" height="10" viewBox="0 0 8 10"><path d="M2 1l4 4-4 4" stroke="#fff" stroke-width="1.6" fill="none"/></svg>
</div>

<div class="abs feature-photo" role="img" aria-label="Dentist treating a patient reclining in the chair"></div>
<h2 class="abs feature-title">We provides higher end dental practice incorporating very new technologies.</h2>
<p class="abs body-text feature-text">Aenean sollicitudin, lorem quis bibendum auctor, nisi elit consequat ipsum, nec sagittis sem nibh id elit. Duis sed odio sit amet nibh vulputate cursus a sit amet mauris. Morbi accumsan ipsum velit. Nam nec tellus a odio tincidunt auctor a ornare odio. Sed non mauris vitae erat consequat</p>

<footer class="abs footer"></footer>
<nav class="abs footer-nav">
  <a href="#">Home</a><a href="#">About</a><a href="#">Services</a><a href="#">Dentistry</a><a href="#">Reviews</a><a href="#">Contact</a>
</nav>
<div class="abs copyright">Copyright © 2014 Ashford Dental Clinic. All rights reserved.</div>
<div class="abs social social--footer" aria-label="Social links"><span></span><span></span></div>
</body>
</html>
```